sydney wedding photography business needs a business card design

we need a business card design for a sydney based wedding photography and videography business. our business name is :golden hour studio and film. our target clients are 24-35 yrs female. our style is candid, organic, natural, dynamic. we are a team of young photographers and videographers, and help brides to create memories that they will cherish for the rest of their lives. the logo will be provided. we want an elegant design that reflects our style, and also want to give a great impression to our clients that we are one of the best studios in sydney and our brand means quality and premium service.

Target Market(s)

bride to be, 24-35 years old, living in sydney and surrunding areas

Industry/Entity Type

Wedding Photography

Contact Information for Business Card

address: 57 tarrant street, glenmore nsw 2047
mobile: 0431872259
phone: (02) 9163 2408
info@tidewillowstudio.net.au
www.tidewillowstudio.net.au
facebook:tidewillowweddings
instagram:tidewillowweddings

Font styles to use
Serif
Sans Serif

Requirements
Nice to have
• maybe add my slogan"memories beyond eternity" if the layout looks good
Should not have
• no black color, not good idea for wedding biz card

```html
<!DOCTYPE html>
<html lang="en">
<head>
<meta charset="utf-8">
<title>Golden Hour Studio and Film – Business Card</title>
<link rel="stylesheet" href="https://fonts.googleapis.com/css2?family=Josefin+Sans:wght@300;400;600&display=swap">
<style>
  :root {
    --page-bg: #ece8e1;
    --card-ivory: #f8f2e4;
    --gold-light: #e6ac19;
    --gold-mid: #d49a12;
    --gold-deep: #a8750c;
    --ink-brown: #4a3414;
    --ink-warm: #5c4320;
  }
  * { box-sizing: border-box; margin: 0; padding: 0; }
  html, body {
    width: 1200px;
    height: 950px;
    overflow: hidden;
    background: var(--page-bg);
    font-family: "Josefin Sans", Arial, sans-serif;
  }
  .sheet {
    position: relative;
    width: 1200px;
    height: 950px;
  }
  .card {
    position: absolute;
    left: 250px;
    width: 700px;
    height: 400px;
    overflow: hidden;
    box-shadow: 0 10px 28px rgba(74, 52, 20, 0.22);
  }
  .card-front { top: 55px; background: var(--card-ivory); }
  .card-back {
    top: 495px;
    background: radial-gradient(ellipse at 60% 55%, var(--gold-light) 0%, var(--gold-mid) 45%, var(--gold-deep) 100%);
  }

  .front-shapes { position: absolute; inset: 0; }

  .front-brand {
    position: absolute;
    left: 120px;
    top: 78px;
    color: var(--gold-deep);
    font-weight: 600;
    font-size: 25px;
    letter-spacing: 0.5px;
    line-height: 1.15;
    width: 240px;
  }

  .holder-name {
    position: absolute;
    left: 60px;
    top: 322px;
    color: var(--ink-brown);
    font-weight: 400;
    font-size: 19px;
    letter-spacing: 2px;
  }

  .contact-list {
    position: absolute;
    right: 42px;
    top: 62px;
    list-style: none;
    color: var(--ink-warm);
    font-weight: 400;
    font-size: 17px;
    line-height: 28px;
  }
  .contact-list li {
    display: flex;
    justify-content: flex-end;
    align-items: center;
    gap: 12px;
  }
  .contact-icon {
    width: 14px;
    height: 14px;
    flex: none;
  }
  .contact-icon.blank { visibility: hidden; }
  .contact-icon.square { background: var(--gold-mid); border-radius: 2px; }

  .back-brand {
    position: absolute;
    left: 0;
    right: 0;
    top: 178px;
    display: flex;
    justify-content: center;
    align-items: center;
    gap: 14px;
    color: var(--ink-brown);
    font-weight: 600;
    font-size: 30px;
    letter-spacing: 0.5px;
  }
  .back-brand-dot {
    width: 26px;
    height: 26px;
    border-radius: 50%;
    background: var(--ink-brown);
  }

  .back-web {
    position: absolute;
    left: 26px;
    top: 40px;
    writing-mode: vertical-rl;
    color: var(--ink-brown);
    font-weight: 300;
    font-size: 15px;
    letter-spacing: 3px;
  }
</style>
</head>
<body>
<main class="sheet">

  <section class="card card-front" aria-label="Business card front">
    <svg class="front-shapes" width="700" height="400" viewBox="0 0 700 400" aria-hidden="true">
      <defs>
        <linearGradient id="gold-panel" x1="0" y1="1" x2="1" y2="0">
          <stop offset="0" stop-color="#a8750c"/>
          <stop offset="0.5" stop-color="#e6ac19"/>
          <stop offset="1" stop-color="#c48c10"/>
        </linearGradient>
      </defs>
      <polygon points="0,170 420,400 0,400" fill="url(#gold-panel)"/>
      <line x1="0" y1="170" x2="420" y2="400" stroke="#d49a12" stroke-width="3"/>
    </svg>

    <div class="front-brand">golden hour studio and film</div>
    <div class="holder-name">CLARA BENNET</div>

    <ul class="contact-list">
      <li>57 tarrant street <span class="contact-icon blank"></span></li>
      <li>glenmore nsw 2047 <span class="contact-icon blank"></span></li>
      <li>(02) 9163 2408
        <svg class="contact-icon" viewBox="0 0 14 14" aria-hidden="true">
          <path d="M3 1 L5.5 1 L6.5 4 L5 5.3 C5.8 7 7 8.2 8.7 9 L10 7.5 L13 8.5 L13 11 C13 12.2 12 13 10.8 13 C5.5 12.6 1.4 8.5 1 3.2 C1 2 1.8 1 3 1 Z" fill="var(--gold-mid)"/>
        </svg>
      </li>
      <li>0431872259
        <svg class="contact-icon" viewBox="0 0 14 14" aria-hidden="true">
          <rect x="3" y="0.5" width="8" height="13" rx="1.5" fill="none" stroke="var(--gold-mid)" stroke-width="1.4"/>
          <circle cx="7" cy="11" r="0.9" fill="var(--gold-mid)"/>
        </svg>
      </li>
      <li>info@tidewillowstudio.net.au <span class="contact-icon blank"></span></li>
      <li>tidewillowweddings <span class="contact-icon square"></span></li>
      <li>tidewillowweddings <span class="contact-icon square"></span></li>
    </ul>
  </section>

  <section class="card card-back" aria-label="Business card back">
    <div class="back-web">www.tidewillowstudio.net.au</div>
    <div class="back-brand">
      <span class="back-brand-dot"></span>
      <span>golden hour studio and film</span>
    </div>
  </section>

</main>
</body>
</html>
```